Brantor Works Business Card

Modern and Professional Business Card for a Med size construction/development company.

See the samples below for the design I like … but I need ideas for incorporating the red company logo while still keeping the clean look of the card samples that are attached.

Logo and tag line on the back … info on the front.

Tagline: Quality Starts from the Ground Up

Target Market(s)

Med-Large General Contractors

Contact Information for Business Card

Brantor Works Limited
42 Fenwick Avenue
Mt. Pearl, NL
A1N 4R9

t: 709-555-0147
f: 709-555-0182
w: www.brantorworks-example.com

Font styles to use
Sans Serif

Colors
fbee3e

Requirements
Must have
• I like the black and yellow designs of the attached samples …. but I'm not sure how to incorporate the red Brantor Works logo into that design??
Nice to have
• Construction safety strips

```html
<!DOCTYPE html>
<html lang="en">
<head>
<meta charset="utf-8">
<title>Brantor Works Business Card</title>
<link rel="stylesheet" href="https://fonts.googleapis.com/css2?family=Nunito:wght@400;600;800&display=swap">
<style>
  :root {
    --backdrop: #2a2a2a;
    --card-red: #e01b24;
    --ink: #111111;
    --paper-white: #ffffff;
    --rule: #7a0d12;
  }
  * { margin: 0; padding: 0; box-sizing: border-box; }
  html, body {
    width: 1200px; height: 917px; overflow: hidden;
    background: var(--backdrop);
    font-family: "Nunito", sans-serif;
  }
  .canvas { position: relative; width: 1200px; height: 917px; }

  .card {
    position: absolute;
    width: 600px; height: 343px;
    background: var(--card-red);
    box-shadow: 0 18px 40px rgba(0,0,0,0.55);
  }
  .card--front { left: 110px; top: 80px; }
  .card--back  { left: 490px; top: 480px; }

  /* Front side */
  .company-name {
    position: absolute; right: 34px; top: 40px;
    width: 260px; text-align: center;
    font-weight: 800; font-size: 26px; line-height: 1.1;
    color: var(--ink); text-transform: uppercase; letter-spacing: 0.5px;
  }
  .person { position: absolute; left: 40px; top: 190px; }
  .person__name { font-weight: 800; font-size: 25px; color: var(--ink); line-height: 1.1; }
  .person__title { font-size: 14px; color: var(--paper-white); margin-top: 2px; }

  .divider {
    position: absolute; left: 40px; right: 34px; top: 246px;
    height: 1px; background: var(--rule);
  }

  .contact-list {
    position: absolute; left: 40px; top: 262px; list-style: none;
  }
  .contact-list li {
    display: flex; align-items: center; gap: 12px;
    font-size: 14px; color: var(--paper-white); height: 21px;
  }
  .contact-list svg { width: 14px; height: 14px; flex: none; }
  .icon-fill { fill: var(--ink); }
  .icon-line { fill: none; stroke: var(--ink); stroke-width: 1.3; }

  .address {
    position: absolute; right: 34px; top: 258px;
    text-align: right; font-size: 13px; line-height: 1.45;
    font-style: normal; color: var(--paper-white);
  }

  /* Back side */
  .brand-lockup {
    position: absolute; left: 0; right: 0; top: 110px; text-align: center;
  }
  .brand-lockup__name {
    font-weight: 800; font-size: 42px; line-height: 1.05;
    color: var(--ink); text-transform: uppercase; letter-spacing: 1px;
  }
  .brand-lockup__tagline {
    margin-top: 18px; font-size: 15px; color: var(--paper-white); letter-spacing: 0.4px;
  }
</style>
</head>
<body>
<main class="canvas">

  <section class="card card--front" aria-label="Business card front">
    <div class="company-name">Brantor Works<br>Limited</div>

    <div class="person">
      <div class="person__name">Morgan Hale</div>
      <div class="person__title">Founder &amp; CEO</div>
    </div>

    <div class="divider"></div>

    <address class="address">
      Brantor Works Limited<br>
      42 Fenwick Avenue<br>
      Harrow Bay, NL A0B 1C2
    </address>

    <ul class="contact-list">
      <li>
        <svg viewBox="0 0 16 16" aria-hidden="true"><path class="icon-fill" d="M1 5c0-2 2-3 7-3s7 1 7 3v1h-3V4.5H4V6H1z M3 7h10l1 7H2z"/><circle cx="8" cy="10.5" r="2" fill="#e01b24"/></svg>
        709-555-0147
      </li>
      <li>
        <svg viewBox="0 0 16 16" aria-hidden="true"><path class="icon-fill" d="M4 1h8v4H4z M1 6h14v6h-3v-2H4v2H1z M5 11h6v4H5z"/></svg>
        709-555-0182
      </li>
      <li>
        <svg viewBox="0 0 16 16" aria-hidden="true"><g class="icon-line"><circle cx="8" cy="8" r="6.5"/><ellipse cx="8" cy="8" rx="2.8" ry="6.5"/><path d="M1.5 8h13M2.6 4.8h10.8M2.6 11.2h10.8"/></g></svg>
        www.brantorworks-example.com
      </li>
    </ul>
  </section>

  <section class="card card--back" aria-label="Business card back">
    <div class="brand-lockup">
      <div class="brand-lockup__name">Brantor Works<br>Limited</div>
      <div class="brand-lockup__tagline">Quality Starts from the Ground Up</div>
    </div>
  </section>

</main>
</body>
</html>
```